BUSINESS CARD DESIGN

NAME- DALE VORSKIN
PHONE NUMER - 555- 714-9082
EMAIL- OFFICE@TRV-GROUNDMAKRZ.COM
BACK OF CARD- SPEACIALIZES IN LAND CLEARING, FORESTRY MUCLHING AND EXCAVATION

Contact Information for Business Card

NAME- DALE VORSKIN PHONE NUMER - 555- 714-9082 EMAIL- OFFICE@TRV-GROUNDMAKRZ.COM BACK OF CARD- SPEACIALIZES IN LAND CLEARING , MUCLHING AND EXCAVATION

```html
<!DOCTYPE html>
<html lang="en">
<head>
<meta charset="utf-8">
<title>Terravine Groundmakrz – Business Card</title>
<link href="https://fonts.googleapis.com/css2?family=Montserrat:wght@400;500;700&display=swap" rel="stylesheet">
<style>
  :root {
    --stage: #1c1c1c;
    --card: #0b0b0b;
    --gold: #f7b416;
    --ink: #ffffff;
    --emboss: #1e1e1e;
    --emboss-edge: #2c2c2c;
    --emboss-text: #3a3a3a;
  }
  * { box-sizing: border-box; margin: 0; padding: 0; }
  html, body { width: 1200px; height: 1200px; overflow: hidden; }
  body {
    background: var(--stage);
    font-family: "Montserrat", sans-serif;
    display: flex;
    flex-direction: column;
    align-items: center;
    justify-content: center;
    gap: 44px;
  }
  .card {
    position: relative;
    width: 900px;
    height: 514px;
    background: var(--card);
    box-shadow: 0 10px 30px rgba(0,0,0,.5);
  }

  /* Back side */
  .card--back {
    display: flex;
    flex-direction: column;
    align-items: center;
    justify-content: center;
    gap: 18px;
  }
  .back-mark {
    width: 110px; height: 110px;
    border-radius: 50%;
    background: var(--emboss);
    box-shadow: inset 1px 1px 0 var(--emboss-edge);
  }
  .back-name {
    font-weight: 700;
    font-size: 38px;
    letter-spacing: 3px;
    color: var(--emboss);
    text-shadow: 1px 1px 0 var(--emboss-edge);
    text-align: center;
    line-height: 1.15;
  }
  .back-services {
    font-weight: 500;
    font-size: 17px;
    letter-spacing: 2px;
    color: var(--emboss-text);
    text-align: center;
    line-height: 1.5;
  }

  /* Front side */
  .brand {
    position: absolute;
    left: 100px; top: 170px;
    width: 280px;
    display: flex;
    flex-direction: column;
    align-items: center;
    gap: 14px;
  }
  .brand-mark {
    width: 70px; height: 70px;
    border-radius: 50%;
    background: var(--gold);
  }
  .brand-name {
    color: var(--gold);
    font-weight: 700;
    font-size: 22px;
    letter-spacing: 1.5px;
    text-align: center;
    line-height: 1.25;
    white-space: nowrap;
  }
  .divider {
    position: absolute;
    left: 392px; top: 168px;
    width: 3px; height: 168px;
    background: var(--gold);
  }
  .person {
    position: absolute;
    left: 420px; top: 168px;
  }
  .person-name {
    color: var(--gold);
    font-weight: 700;
    font-size: 38px;
    letter-spacing: 1px;
    line-height: 1;
  }
  .person-title {
    color: var(--ink);
    font-size: 22px;
    letter-spacing: .5px;
    margin-top: 6px;
  }
  .contacts {
    list-style: none;
    margin-top: 14px;
    display: flex;
    flex-direction: column;
    gap: 8px;
  }
  .contacts li {
    display: flex;
    align-items: center;
    gap: 12px;
    color: var(--ink);
    font-size: 21px;
    letter-spacing: .5px;
    white-space: nowrap;
  }
  .contacts svg { width: 20px; height: 20px; fill: var(--gold); flex: none; }
  .address {
    position: absolute;
    left: 120px; top: 392px;
    color: var(--ink);
    font-size: 23px;
    letter-spacing: .5px;
    word-spacing: 2px;
  }
</style>
</head>
<body>

  <section class="card card--back" aria-label="Card back">
    <div class="back-mark"></div>
    <p class="back-name">TERRAVINE<br>GROUNDMAKRZ LLC</p>
    <p class="back-services">SPECIALIZES IN LAND CLEARING,<br>FORESTRY MULCHING AND EXCAVATION</p>
  </section>

  <section class="card card--front" aria-label="Card front">
    <div class="brand">
      <div class="brand-mark"></div>
      <p class="brand-name">TERRAVINE<br>GROUNDMAKRZ LLC</p>
    </div>

    <div class="divider"></div>

    <div class="person">
      <h1 class="person-name">DALE VORSKIN</h1>
      <p class="person-title">Managing Director</p>
      <ul class="contacts">
        <li>
          <svg viewBox="0 0 24 24" aria-hidden="true"><path d="M6.6 10.8a15 15 0 0 0 6.6 6.6l2.2-2.2c.3-.3.7-.4 1-.2 1.1.4 2.3.6 3.6.6.6 0 1 .4 1 1V20c0 .6-.4 1-1 1A17 17 0 0 1 3 4c0-.6.4-1 1-1h3.5c.6 0 1 .4 1 1 0 1.3.2 2.5.6 3.6.1.3 0 .7-.2 1z"/></svg>
          555- 714-9082
        </li>
        <li>
          <svg viewBox="0 0 24 24" aria-hidden="true"><path d="M2 5h20v2l-10 6L2 7z M2 9l10 6 10-6v10H2z"/></svg>
          OFFICE@TRV-GROUNDMAKRZ.COM
        </li>
        <li>
          <svg viewBox="0 0 24 24" aria-hidden="true"><path d="M12 2a10 10 0 1 0 0 20 10 10 0 0 0 0-20zm-1 17.9A8 8 0 0 1 4.1 11H7c.2 3.2 1.6 6.3 4 8.9zM7 9H4.3A8 8 0 0 1 11 4.1C8.6 6.7 7.2 9 7 9zm2 2h6c-.2 2.8-1.3 5.3-3 7.4-1.7-2.1-2.8-4.6-3-7.4zm0-2c.2-2.2 1.3-4.3 3-6.1 1.7 1.8 2.8 3.9 3 6.1zm4 10.9c2.4-2.6 3.8-5.7 4-8.9h2.9a8 8 0 0 1-6.9 8.9zM17 9c-.2-1.9-1.6-4.3-4-4.9A8 8 0 0 1 19.7 9z"/></svg>
          WWW.TRV-GROUNDMAKRZ.COM
        </li>
      </ul>
    </div>

    <p class="address">418 Harbor Ridge Rd, #112&nbsp; Kailua, HI 96734</p>
  </section>

</body>
</html>
```